Design a poster that illustrates the six central pillars of our school district's efforts with students. The attached PDF outlines the six main competencies we aim for students to possess upon graduation. Each of the 6 has 3 bullet points for the poster as well. The title is "Profile of a Trailblazer". Our mascot is this attached winged wheel. The overall concept is that staff take kids when they are young and develop these 6 things when they graduate. Our colors are navy, red, and white. We will make this poster in a variety of sizes in offices, classrooms, and in digital spaces as well. On the PDF - ignore the column that says "Synthesis". That has nothing to do with this poster.

The district is Harlow Creek Public Schools https://www.harlowcreek-schools.example/

```html
<!DOCTYPE html>
<html lang="en">
<head>
<meta charset="utf-8">
<title>Profile of a Trailblazer</title>
<link rel="stylesheet" href="https://fonts.googleapis.com/css2?family=Archivo:wght@300;900&family=Barlow+Condensed:wght@600&display=swap">
<style>
  :root {
    --backdrop: #bfc0c2;
    --navy: #0c0d3d;
    --red: #a51f26;
    --white: #ffffff;
  }
  * { margin: 0; padding: 0; box-sizing: border-box; }
  html, body { width: 924px; height: 1200px; overflow: hidden; }
  body { background: var(--backdrop); position: relative; font-family: "Barlow Condensed", "Arial Narrow", sans-serif; }

  .poster { position: absolute; left: 90px; top: 74px; width: 743px; height: 1050px; background: var(--navy); }
  .poster-header { position: absolute; left: 0; top: 0; width: 743px; height: 191px; background: var(--white); }

  .district-mark { position: absolute; left: 78px; top: 58px; width: 210px; display: flex; align-items: center; gap: 12px; }
  .district-mark-dot { flex: none; width: 56px; height: 56px; border-radius: 50%; background: var(--red); }
  .district-name { font-family: "Barlow Condensed", "Arial Narrow", sans-serif; font-weight: 600; font-size: 26px; line-height: 1.05; color: var(--navy); }

  .poster-title { position: absolute; left: 376px; top: 80px; color: var(--navy); font-family: "Archivo", Arial, sans-serif; }
  .poster-title-lead { display: block; font-weight: 300; font-size: 37px; line-height: 1; letter-spacing: 1px; }
  .poster-title-main { display: block; font-weight: 900; font-size: 45px; line-height: 1.1; letter-spacing: 1px; }

  .pillar { position: absolute; width: 313px; height: 223px; border: 3px solid var(--red); border-radius: 16px; }
  .pillar-name { position: absolute; top: -20px; left: 17px; padding: 0 6px; background: var(--navy); color: var(--white); font-size: 29px; line-height: 34px; font-weight: 600; }
  .pillar-traits { list-style: none; position: absolute; left: 12px; right: 8px; top: 22px; color: var(--white); font-size: 20px; line-height: 23px; letter-spacing: -0.2px; }
  .pillar-traits li { position: relative; padding-left: 11px; margin-bottom: 14px; }
  .pillar-traits li::before { content: "•"; position: absolute; left: 0; top: -1px; }
  .pillar-traits--spaced li { margin-bottom: 20px; }
  .pillar-traits--tight li { margin-bottom: 10px; }

  .col-left { left: 54px; }
  .col-right { left: 399px; }
  .row-1 { top: 231px; }
  .row-2 { top: 508px; }
  .row-3 { top: 784px; }
</style>
</head>
<body>
  <div class="poster">
    <header class="poster-header">
      <div class="district-mark">
        <span class="district-mark-dot"></span>
        <span class="district-name">Harlow Creek Public Schools</span>
      </div>
      <h1 class="poster-title">
        <span class="poster-title-lead">PROFILE OF A</span>
        <span class="poster-title-main">TRAILBLAZER</span>
      </h1>
    </header>

    <section class="pillar col-left row-1">
      <h2 class="pillar-name">Communicator</h2>
      <ul class="pillar-traits pillar-traits--spaced">
        <li>Expresses ideas clearly<br>and respectfully (written &amp; verbal).</li>
        <li>Listens actively and understands diverse perspectives.</li>
        <li>Adjusts communication to suit<br>the audience and context.</li>
      </ul>
    </section>

    <section class="pillar col-right row-1">
      <h2 class="pillar-name">Critical Thinker</h2>
      <ul class="pillar-traits">
        <li>Questions, analyzes, and evaluates information from multiple sources.</li>
        <li>Identifies and solves complex<br>problems creatively.</li>
        <li>Uses evidence and diverse<br>perspectives to form reasoned conclusions and make informed</li>
      </ul>
    </section>

    <section class="pillar col-left row-2">
      <h2 class="pillar-name">Responsible</h2>
      <ul class="pillar-traits pillar-traits--spaced">
        <li>Takes ownership of actions, choices, and commitments.</li>
        <li>Manages time, resources, and self to meet expectations.</li>
        <li>Acts with integrity and advocates for self and others.</li>
      </ul>
    </section>

    <section class="pillar col-right row-2">
      <h2 class="pillar-name">Adaptable</h2>
      <ul class="pillar-traits pillar-traits--tight">
        <li>Responds productively to new situations, challenges, and feedback.</li>
        <li>Learns from new experiences and applies prior knowledge in evolving contexts.</li>
        <li>Adjusts behavior and approach to effectively engage with diverse groups and environments.</li>
      </ul>
    </section>

    <section class="pillar col-left row-3">
      <h2 class="pillar-name">Collaborator</h2>
      <ul class="pillar-traits pillar-traits--tight">
        <li>Contributes effectively and<br>cooperatively to shared goals</li>
        <li>Listens actively and values diverse ideas and perspectives.</li>
        <li>Engages respectfully, compromising and leading when<br>appropriate.</li>
      </ul>
    </section>

    <section class="pillar col-right row-3">
      <h2 class="pillar-name">Compassionate</h2>
      <ul class="pillar-traits pillar-traits--tight">
        <li>Understands and acknowledges others' feelings, perspectives, and<br>experiences.</li>
        <li>Responds with kindness, patience, and support.</li>
        <li>Seeks to connect with and contribute positively to the well-being of others</li>
      </ul>
    </section>
  </div>
</body>
</html>
```